Verodex business card

Business card for sustainable investment company called "Verodex". Verodex is an exchange platform selling carbon credits between buyers and sellers. Carbon Credits are an environmental commodity for reducing global carbon emissions.

the card should obviously have our logo and the theme should be sustainability/environment mixed with a trading platform.

Contact Information for Business Card

Logo, Name, Title, Phone, Email

Colors
0054AA
0677BA
7BADD7
CADEEF
E8F1F8
0094D4
00A9DD
6FCCEA
C7EBF8
E9F6FB
00AB8E
00BBA5
67D7C9
C6EFE9
E9F9F6
59FF00
82FF00
B8FF75
E3FFCB
F4FFEA

```html
<!DOCTYPE html>
<html lang="en">
<head>
<meta charset="utf-8">
<title>Verodex Business Card</title>
<link href="https://fonts.googleapis.com/css2?family=Arimo:wght@400;700&display=swap" rel="stylesheet">
<style>
  :root {
    --backdrop: #cadeef;
    --card-light: #e9f6fb;
    --card-dark: #0054aa;
    --card-edge: #7badd7;
    --ink: #0054aa;
    --ink-soft: #0677ba;
    --accent: #00ab8e;
    --accent-bright: #59ff00;
    --paper: #e9f9f6;
  }
  * { margin: 0; padding: 0; box-sizing: border-box; }
  html, body { width: 1200px; height: 976px; overflow: hidden; }
  body {
    background: var(--backdrop);
    font-family: "Arimo", Arial, sans-serif;
    color: var(--ink);
    position: relative;
  }
  .card {
    position: absolute;
    top: 333px;
    width: 540px;
    height: 310px;
    border-radius: 3px;
    overflow: hidden;
    box-shadow: 0 14px 30px rgba(0, 84, 170, 0.18);
  }
  .card--front {
    left: 40px;
    background: var(--card-light);
    border-bottom: 4px solid var(--accent);
  }
  .card--back {
    left: 620px;
    background: linear-gradient(135deg, var(--card-dark) 0%, var(--ink-soft) 55%, var(--accent) 100%);
    border-bottom: 4px solid var(--accent-bright);
  }

  .brand {
    position: absolute;
    display: flex;
    align-items: center;
    gap: 10px;
    font-weight: 700;
    line-height: 1;
    white-space: nowrap;
  }
  .brand__square { background: var(--accent); flex: none; }

  .card--front .brand { top: 56px; right: 44px; font-size: 24px; color: var(--ink); }
  .card--front .brand__square { width: 18px; height: 18px; }

  .person { position: absolute; left: 44px; top: 102px; }
  .person__name {
    font-size: 28px; font-weight: 700; letter-spacing: 0.5px; line-height: 1;
    color: var(--ink);
  }
  .person__title {
    font-size: 15px; font-weight: 700; margin-top: 6px; line-height: 1.2;
    color: var(--ink-soft);
  }

  .rule {
    position: absolute;
    left: 40px; right: 40px; top: 178px;
    height: 3px;
    background: var(--accent);
  }

  .contact { position: absolute; left: 44px; top: 196px; list-style: none; }
  .contact__item {
    display: flex; align-items: center; gap: 8px;
    font-weight: 700; line-height: 1; color: var(--ink);
  }
  .contact__item--phone { font-size: 17px; margin-bottom: 9px; }
  .contact__item--email { font-size: 14px; }
  .contact__icon { width: 14px; height: 14px; flex: none; }

  .website {
    position: absolute; right: 44px; bottom: 30px;
    font-size: 14px; font-weight: 700; letter-spacing: 0.3px; line-height: 1;
    color: var(--ink);
  }

  .card--back .brand {
    top: 50%; left: 50%;
    transform: translate(-50%, -50%);
    font-size: 56px; gap: 18px; letter-spacing: 1px;
    color: var(--paper);
  }
  .card--back .brand__square { width: 40px; height: 40px; background: var(--accent-bright); }
</style>
</head>
<body>
  <section class="card card--front" aria-label="Business card front">
    <div class="brand"><span class="brand__square"></span>Verodex</div>
    <div class="person">
      <h1 class="person__name">MARCUS HALE</h1>
      <p class="person__title">Founder &amp; CEO</p>
    </div>
    <div class="rule"></div>
    <ul class="contact">
      <li class="contact__item contact__item--phone">
        <svg class="contact__icon" viewBox="0 0 24 24" aria-hidden="true"><path fill="#00ab8e" d="M6.6 10.8a15 15 0 0 0 6.6 6.6l2.2-2.2a1 1 0 0 1 1-.25 11.4 11.4 0 0 0 3.6.57 1 1 0 0 1 1 1V20a1 1 0 0 1-1 1A17 17 0 0 1 3 4a1 1 0 0 1 1-1h3.5a1 1 0 0 1 1 1c0 1.25.2 2.45.57 3.57a1 1 0 0 1-.25 1z"/></svg>
        (555) 204-7716
      </li>
      <li class="contact__item contact__item--email">
        <svg class="contact__icon" viewBox="0 0 24 24" aria-hidden="true"><path fill="#00ab8e" d="M2 5h20v14H2z"/><path fill="none" stroke="#e9f6fb" stroke-width="1.8" d="M2.5 5.5 12 13l9.5-7.5"/></svg>
        office@verodex.com
      </li>
    </ul>
    <p class="website">www.Verodex.com</p>
  </section>

  <section class="card card--back" aria-label="Business card back">
    <div class="brand"><span class="brand__square"></span>VERODEX</div>
  </section>
</body>
</html>
```